One Page Menu for Food Truck centered on healthy and sustainable eating

This project is a menu for Dorvey's - a mobile catering company centered around healthy and sustainable eating.

The menu will be distributed in PDF and print formats. Because of the different mediums, it needs to be one page size.

Our menu will feature three healthy wraps:

The Garden - $7
Filled with Hummus, Fresh Roasted Peppers, Sliced Cucumber, Spinach, Mint Leaves, and Za'tar. (Our vegan option)

The Steak - $8
Filled with Seared Flat Iron Steak, Caramelized Onions, and Blue Cheese.

The Mediterranean - $7
Filled with Marinated Artichoke Hearts, Kalamata Olives, Pepperoncini, and Fresh Squeezed Lemon with a Feta Cheese and Labne Spread.

Dorvey's also provides:

Aquas Frescas - $3
A Refreshing Daily Blend of Fruit and Vegetable Purée, Chia Seeds, and Agave Nectar

Jamaica Blue Mountain Reserve Coffee - $2

Water - $1

The design should reflect Dorvey's colors of Orange and Green. We would also like a design that incorporates urban gardening, but how is up to you.

Please see website for company - dorvey.org

Industry/Entity Type

Catering

Requirements
Must have
• Menu items, short descriptions, company logo, Green Colors and Orange Colors

```html
<!DOCTYPE html>
<html lang="en">
<head>
<meta charset="utf-8">
<title>Dorvey's Menu</title>
<link rel="stylesheet" href="https://fonts.googleapis.com/css2?family=Kanit:wght@500;600&family=Didact+Gothic&family=Courier+Prime&display=swap">
<style>
  :root {
    --leaf-green: #7cc04a;
    --leaf-green-soft: #a6d57f;
    --brand-orange: #f58a1f;
    --panel-white: #ffffff;
    --ink: #111111;
    --arc-ink: #1d1d1d;
    --fruit-orange: #f29a2e;
    --fruit-red: #c8362a;
    --fruit-green: #5f8f2e;
  }
  * { margin: 0; padding: 0; box-sizing: border-box; }
  html, body { width: 927px; height: 1200px; overflow: hidden; }
  body { background: var(--leaf-green); font-family: "Didact Gothic", sans-serif; color: var(--ink); }
  .menu { position: relative; width: 927px; height: 1200px; overflow: hidden; background: var(--leaf-green); }

  .frame-band { position: absolute; background: var(--brand-orange); }
  .frame-band--left { left: 88px; top: 178px; width: 132px; height: 700px; }
  .frame-band--right { left: 736px; top: 178px; width: 130px; height: 700px; }

  .menu-panel { position: absolute; left: 218px; top: 175px; width: 520px; height: 720px; background: var(--panel-white); }

  .brand-name {
    position: absolute; left: 40px; top: 22px;
    font-family: "Kanit", sans-serif; font-weight: 600;
    font-size: 150px; line-height: 1; color: var(--brand-orange); letter-spacing: -2px;
  }

  .arc-text { position: absolute; left: 0; top: 0; width: 927px; height: 1200px; pointer-events: none; }
  .arc-text text { font-family: "Courier Prime", monospace; font-size: 19px; fill: var(--arc-ink); letter-spacing: 3px; }

  .menu-items { position: absolute; left: 218px; top: 204px; width: 520px; text-align: center; z-index: 2; }
  .item { margin-bottom: 24px; }
  .item-name { font-family: "Kanit", sans-serif; font-weight: 600; font-size: 19px; line-height: 24px; }
  .item-desc { font-size: 16.5px; line-height: 22px; }
  .item--inline { font-size: 17px; margin-bottom: 20px; }
  .item--inline .item-name { display: inline; font-size: 19px; }
  .price { font-family: "Didact Gothic", sans-serif; font-weight: 400; }

  .divider { width: 44px; height: 22px; margin: -17px auto 15px; background: var(--leaf-green-soft); border-radius: 50% 50% 40% 40%; }

  .fruit-photo { position: absolute; left: 0; top: 0; width: 927px; height: 1200px; z-index: 1; }

  .site-url {
    position: absolute; left: 240px; top: 1116px; z-index: 2;
    font-family: "Kanit", sans-serif; font-weight: 600; font-size: 22px; color: var(--panel-white);
  }
</style>
</head>
<body>
<main class="menu">
  <div class="frame-band frame-band--left"></div>
  <div class="frame-band frame-band--right"></div>
  <div class="menu-panel"></div>

  <h1 class="brand-name">Dorvey's</h1>

  <svg class="arc-text" viewBox="0 0 927 1200" aria-hidden="true">
    <defs>
      <path id="arc-right" d="M520 160 Q760 200 875 455"/>
      <path id="arc-left" d="M95 712 Q95 420 165 282"/>
    </defs>
    <text><textPath href="#arc-right">FEATURING THREE HEALTHY WRAPS</textPath></text>
    <text><textPath href="#arc-left">HEALTHY SUSTAINABLE EATING</textPath></text>
  </svg>

  <svg class="fruit-photo" viewBox="0 0 927 1200" role="img" aria-label="Photo of a heap of fresh fruit: pineapple, oranges, apples, avocados, limes and kiwano">
    <defs>
      <linearGradient id="fruit-tone" x1="0" y1="0" x2="1" y2="1">
        <stop offset="0" stop-color="var(--fruit-orange)"/>
        <stop offset="0.45" stop-color="var(--fruit-red)"/>
        <stop offset="0.7" stop-color="var(--fruit-green)"/>
        <stop offset="1" stop-color="var(--fruit-orange)"/>
      </linearGradient>
    </defs>
    <path fill="url(#fruit-tone)" d="M0 1200 L0 1010 L60 960 L150 880 L218 800 L300 745 L420 728 L560 730 L700 745 L745 680 L790 560 L840 470 L890 430 L927 440 L927 1200 Z"/>
  </svg>

  <section class="menu-items">
    <article class="item">
      <h2 class="item-name">The Garden</h2>
      <p class="item-desc">Filled with Hummus, Fresh Roasted Peppers, Sliced<br>Cucumber, Spinach, Mint Leaves, and Za'tar.<br>(Our vegan option)&nbsp; $7</p>
    </article>
    <article class="item">
      <h2 class="item-name">The Steak</h2>
      <p class="item-desc">Filled with Seared Flat Iron Steak, Caramelized Onions,<br>and Blue Cheese&nbsp; $8</p>
    </article>
    <article class="item">
      <h2 class="item-name">The Mediterranean</h2>
      <p class="item-desc">Filled with Marinated Artichoke Hearts, Kalamata Olives,<br>Pepperoncini, and Fresh Squeezed Lemon with a Feta<br>Cheese and Labne Spread&nbsp; $7</p>
    </article>
    <div class="divider" role="img" aria-label="Small leaf sprig divider"></div>
    <article class="item">
      <h2 class="item-name">Aquas Frescas</h2>
      <p class="item-desc">A Refreshing Daily Blend of Fruit and Vegetable Purée,<br>Chia Seeds, and Agave Nectar&nbsp; $3</p>
    </article>
    <p class="item item--inline"><span class="item-name">Jamaica Blue Mountain Reserve Coffee</span> <span class="price">$2</span></p>
    <p class="item item--inline"><span class="item-name">Water</span> <span class="price">$1</span></p>
  </section>

  <p class="site-url">www.dorvey.org</p>
</main>
</body>
</html>
```